Marrowby Water Taxi and Transport Business Card

I need business cards for my new water taxi and freight transport business I have started here in Kodiak Alaska. Kodiak is a remote island in the middle of the gulf of Alaska. There are seven native villages around the island and Kodiak is the #2 fishing port in the United States. We also have the largest Coast Guard Base in the U.S. My company will be providing water taxi and freight transport logistics to the villages and many hunting and fishing lodges as well as remote properties around the island.

I would like a business card that isn't status quo, something that stands out, either in feel or appearance. I do like clean minimal designs but it needs to have the necessary contact info on it.

Target Market(s)

remote lodge / property owners, residents of the many villages around Kodiak and any one wanting to enjoy the great outdoors of Kodiak Alaska

Industry/Entity Type

Business

Contact Information for Business Card

I like clean simple designs that aren't cluttered but still provide the necessary information

Colors
0255a3
3277b5
33a4d5
9bcb3c
add136
fbed22
ffc214
f78f20
f37122

Requirements
Must have
• logo and contact info
• Captain Mason Elwick
• www.marrowbyferryline.com
• mason@marrowbyferryline.com

```html
<!DOCTYPE html>
<html lang="en">
<head>
<meta charset="utf-8">
<title>Marrowby Water Taxi and Transport – Business Card</title>
<link rel="stylesheet" href="https://fonts.googleapis.com/css2?family=Open+Sans:wght@400;600;700&display=swap">
<style>
  :root {
    --navy: #1a5aa8;
    --brand-blue: #0255a3;
    --sky: #33a4d5;
    --sun: #f78f20;
    --white: #ffffff;
    --paper: #f4f5f6;
    --stage: #e6e7e9;
    --photo-top: #3f86d6;
    --photo-mid: #2a6fc0;
    --photo-deep: #123f80;
    --ink-muted: #5a6470;
  }
  * { box-sizing: border-box; margin: 0; padding: 0; }
  html, body {
    width: 1200px; height: 900px; overflow: hidden;
    background: var(--stage);
    font-family: "Open Sans", Arial, sans-serif;
  }
  .canvas { position: relative; width: 1200px; height: 900px; }

  .card {
    position: absolute; width: 560px; height: 320px;
    border-radius: 4px; overflow: hidden;
    box-shadow: 0 6px 18px rgba(0,0,0,.18);
  }

  /* Front face */
  .card--front { left: 110px; top: 90px; }
  .front__photo {
    position: absolute; inset: 0;
    background: linear-gradient(180deg, var(--photo-top) 0%, #8fbbe6 38%, var(--photo-mid) 52%, var(--photo-deep) 100%);
  }
  .front__brand {
    position: absolute; left: 40px; top: 44px; width: 300px;
    color: var(--white); font-weight: 600; font-size: 28px; line-height: 1.15;
    letter-spacing: .5px;
  }

  /* Back face */
  .card--back { left: 530px; top: 490px; background: var(--paper); }
  .back__brand {
    position: absolute; left: 0; right: 0; top: 62px;
    display: flex; align-items: center; justify-content: center; gap: 14px;
  }
  .brand__dot { width: 26px; height: 26px; border-radius: 50%; background: var(--sun); flex: none; }
  .brand__name {
    color: var(--brand-blue); font-weight: 700; font-size: 26px; line-height: 1.15;
    text-align: left; width: 230px;
  }
  .back__rule { position: absolute; left: 0; right: 0; top: 178px; height: 6px; background: var(--sky); }
  .back__band {
    position: absolute; left: 0; right: 0; top: 192px; bottom: 0;
    background: var(--navy); color: var(--white);
    padding: 22px 0 0 150px;
  }
  .contact__name { font-weight: 700; font-size: 19px; margin-bottom: 10px; }
  .contact__line { display: flex; align-items: center; gap: 9px; font-size: 14px; line-height: 1.65; }
  .contact__icon { width: 13px; height: 13px; flex: none; }
</style>
</head>
<body>
<main class="canvas">

  <section class="card card--front" aria-label="Card front">
    <div class="front__photo" role="img" aria-label="Photograph of a water taxi boat cruising across a blue bay toward snow-capped mountains"></div>
    <p class="front__brand">Marrowby Water Taxi &amp; Transport</p>
  </section>

  <section class="card card--back" aria-label="Card back">
    <div class="back__brand">
      <span class="brand__dot"></span>
      <p class="brand__name">Marrowby Water Taxi &amp; Transport</p>
    </div>
    <div class="back__rule"></div>
    <div class="back__band">
      <p class="contact__name">Captain Mason Elwick</p>
      <p class="contact__line">
        <svg class="contact__icon" viewBox="0 0 16 16" aria-hidden="true">
          <rect x="1" y="3" width="14" height="10" fill="none" stroke="#fff" stroke-width="1.5"/>
          <path d="M1 3 L8 9 L15 3" fill="none" stroke="#fff" stroke-width="1.5"/>
        </svg>
        mason@marrowbyferryline.com
      </p>
      <p class="contact__line">
        <svg class="contact__icon" viewBox="0 0 16 16" aria-hidden="true">
          <path d="M6.5 9.5 L9.5 6.5 M7 4.5 L9 2.5 a2.5 2.5 0 0 1 3.5 3.5 L10.5 8 M5.5 8 L3.5 10 a2.5 2.5 0 0 0 3.5 3.5 L9 11.5" fill="none" stroke="#fff" stroke-width="1.5" stroke-linecap="round"/>
        </svg>
        www.marrowbyferryline.com
      </p>
    </div>
  </section>

</main>
</body>
</html>
```